Slick Boot Gig - 20 Years of Funk

I'm with a funk band called Slick Boot. We are celebrating our 20 year anniversary with a show on August 3, 2024. We would like some banners made for social media to help promote the gig. I'm attaching some examples of our 10 year anniversary gig so you can at least get an idea of what we are looking for.

Here's the text for the banners:
SLICK BOOT Anniversary Gig - 20 Years of Funk!
Saturday, August 10, 2024
with special guest: Marco Delven
Doors at 7pm, Show at 8pm

We would like three sizes:
1920 x 1005 pixels
1080 x 1080 pixels
1080 x 1920 pixels

You can check out our website for more ideas of our graphic style, etc.. www.slickbootband.example

```html
<!DOCTYPE html>
<html lang="en">
<head>
<meta charset="utf-8">
<title>Slick Boot – 20 Years of Funk banners</title>
<link href="https://fonts.googleapis.com/css2?family=Montserrat:wght@400;500;600;700;800&display=swap" rel="stylesheet">
<style>
  :root {
    --board: #d6d6d6;
    --purple-deep: #2e0b4f;
    --purple: #4a1670;
    --pink: #e2409a;
    --cyan: #17b3d8;
    --lime: #c4dd1f;
    --white: #ffffff;
    --ink: #111111;
  }
  * { box-sizing: border-box; margin: 0; padding: 0; }
  html, body { width: 1200px; height: 1200px; overflow: hidden; }
  body {
    background: var(--board);
    font-family: "Montserrat", sans-serif;
    position: relative;
  }
  .banner {
    position: absolute;
    overflow: hidden;
    background:
      radial-gradient(ellipse 55% 45% at 50% 55%, var(--purple-deep) 0%, rgba(46,11,79,0) 100%),
      linear-gradient(135deg, var(--pink) 0%, var(--purple) 30%, var(--purple-deep) 50%, var(--purple) 70%, var(--cyan) 100%);
  }
  .banner--story {
    left: 87px; top: 227px; width: 352px; height: 626px;
    background:
      radial-gradient(ellipse 70% 35% at 50% 62%, var(--purple-deep) 0%, rgba(46,11,79,0) 100%),
      radial-gradient(ellipse 40% 25% at 10% 15%, var(--pink) 0%, rgba(226,64,154,0) 100%),
      radial-gradient(ellipse 40% 25% at 90% 10%, var(--cyan) 0%, rgba(23,179,216,0) 100%),
      radial-gradient(ellipse 40% 25% at 5% 92%, var(--cyan) 0%, rgba(23,179,216,0) 100%),
      radial-gradient(ellipse 40% 25% at 95% 90%, var(--pink) 0%, rgba(226,64,154,0) 100%),
      var(--purple);
  }
  .banner--wide {
    left: 487px; top: 227px; width: 626px; height: 328px;
    background:
      radial-gradient(ellipse 35% 55% at 50% 45%, var(--purple-deep) 0%, rgba(46,11,79,0) 100%),
      radial-gradient(ellipse 25% 45% at 8% 10%, var(--cyan) 0%, rgba(23,179,216,0) 100%),
      radial-gradient(ellipse 25% 45% at 92% 15%, var(--pink) 0%, rgba(226,64,154,0) 100%),
      radial-gradient(ellipse 25% 45% at 5% 90%, var(--pink) 0%, rgba(226,64,154,0) 100%),
      radial-gradient(ellipse 25% 45% at 95% 85%, var(--cyan) 0%, rgba(23,179,216,0) 100%),
      var(--purple);
  }
  .banner--square {
    left: 487px; top: 620px; width: 352px; height: 352px;
    background:
      radial-gradient(ellipse 40% 40% at 50% 45%, var(--purple-deep) 0%, rgba(46,11,79,0) 100%),
      radial-gradient(ellipse 35% 30% at 10% 10%, var(--pink) 0%, rgba(226,64,154,0) 100%),
      radial-gradient(ellipse 35% 30% at 85% 5%, var(--cyan) 0%, rgba(23,179,216,0) 100%),
      radial-gradient(ellipse 35% 30% at 10% 85%, var(--cyan) 0%, rgba(23,179,216,0) 100%),
      radial-gradient(ellipse 35% 30% at 95% 80%, var(--pink) 0%, rgba(226,64,154,0) 100%),
      var(--purple);
  }
  .singer-photo {
    position: absolute;
    border-radius: 40% 40% 6% 6%;
    background: linear-gradient(160deg, rgba(60,200,210,0.55) 0%, rgba(150,140,170,0.6) 40%, rgba(230,110,190,0.6) 75%, rgba(60,20,90,0) 100%);
    -webkit-mask-image: linear-gradient(to bottom, #000 70%, transparent 100%);
            mask-image: linear-gradient(to bottom, #000 70%, transparent 100%);
  }
  .banner--story .singer-photo { left: 55px; top: 39px; width: 240px; height: 288px; }
  .banner--wide .singer-photo { left: 31px; top: 20px; width: 284px; height: 308px; }
  .banner--square .singer-photo { left: 155px; top: 14px; width: 197px; height: 338px; border-radius: 45% 0 0 0; }
  .band-name {
    position: absolute;
    color: var(--lime);
    font-weight: 800;
    white-space: nowrap;
    letter-spacing: -0.5px;
  }
  .banner--story .band-name { left: 66px; top: 236px; font-size: 34px; }
  .banner--wide .band-name { left: 33px; top: 222px; font-size: 40px; }
  .band-badge {
    position: absolute; left: 25px; top: 19px; width: 84px; height: 84px;
    border-radius: 50%;
    background: var(--ink);
    border: 5px solid var(--lime);
    display: flex; align-items: center; justify-content: center;
  }
  .band-badge__name { color: var(--lime); font-weight: 800; font-size: 13px; white-space: nowrap; }
  .event-badge { position: absolute; display: block; }
  .banner--story .event-badge { left: 31px; top: 316px; width: 290px; }
  .banner--wide .event-badge { left: 337px; top: 33px; width: 258px; }
  .banner--square .event-badge { left: 75px; top: 131px; width: 201px; }
  .event-badge text { font-family: "Montserrat", sans-serif; }
</style>
</head>
<body>

<svg width="0" height="0" style="position:absolute" aria-hidden="true">
  <defs>
    <symbol id="event-badge" viewBox="0 0 400 390">
      <path d="M 75 42 Q 200 -38 325 42 L 365 42 Q 368 62 385 66 Q 398 68 398 80 L 398 282 Q 398 296 385 297 Q 368 300 365 318 L 330 318 Q 200 440 70 318 L 35 318 Q 32 300 15 297 Q 2 296 2 282 L 2 80 Q 2 68 15 66 Q 32 62 35 42 Z"
            fill="#2e0b4f" stroke="#ffffff" stroke-width="4"/>
      <path id="arc-top" d="M 105 42 Q 200 -10 295 42" fill="none"/>
      <path id="arc-doors" d="M 95 305 Q 200 365 305 305" fill="none"/>
      <path id="arc-show" d="M 100 332 Q 200 400 300 332" fill="none"/>
      <text fill="#ffffff" font-size="18" font-weight="600" letter-spacing="3">
        <textPath href="#arc-top" startOffset="50%" text-anchor="middle">· ANNIVERSARY ·</textPath>
      </text>
      <text x="200" y="80" text-anchor="middle" fill="#ffffff" font-size="50" font-weight="800">GIG</text>
      <text x="200" y="140" text-anchor="middle" fill="#c4dd1f" font-size="64" font-weight="800">20 YEARS</text>
      <text x="200" y="189" text-anchor="middle" fill="#ffffff" font-size="39" font-weight="800">OF FUNK!</text>
      <text x="200" y="222" text-anchor="middle" font-size="21">
        <tspan fill="#ffffff" font-weight="500">SATURDAY, </tspan><tspan fill="#c4dd1f" font-weight="800">AUGUST 10, 2024</tspan>
      </text>
      <circle cx="60" cy="262" r="3" fill="#ffffff"/>
      <circle cx="340" cy="262" r="3" fill="#ffffff"/>
      <text x="186" y="258" text-anchor="end" fill="#ffffff" font-size="16" font-weight="400">With Special</text>
      <text x="186" y="280" text-anchor="end" fill="#ffffff" font-size="16" font-weight="400">Guest:</text>
      <line x1="199" y1="236" x2="199" y2="288" stroke="#ffffff" stroke-width="1.5"/>
      <text x="212" y="257" fill="#c4dd1f" font-size="27" font-weight="800">Marco</text>
      <text x="212" y="288" fill="#c4dd1f" font-size="27" font-weight="800">Delven</text>
      <text font-size="20" font-weight="500" fill="#ffffff" letter-spacing="1">
        <textPath href="#arc-doors" startOffset="50%" text-anchor="middle">Doors at <tspan fill="#c4dd1f" font-weight="800">7pm,</tspan></textPath>
      </text>
      <text font-size="20" font-weight="500" fill="#ffffff" letter-spacing="2">
        <textPath href="#arc-show" startOffset="50%" text-anchor="middle"><tspan fill="#c4dd1f" font-weight="800">SHOW</tspan> at <tspan fill="#c4dd1f" font-weight="800">8pm</tspan></textPath>
      </text>
    </symbol>
  </defs>
</svg>

<section class="banner banner--story">
  <div class="singer-photo" role="img" aria-label="Photo of the band's singer performing at a microphone stand, tinted pink and cyan"></div>
  <div class="band-name">Slick Boot</div>
  <svg class="event-badge" viewBox="0 0 400 390" role="img" aria-label="Anniversary Gig, 20 Years of Funk! Saturday, August 10, 2024. With special guest Marco Delven. Doors at 7pm, show at 8pm"><use href="#event-badge"/></svg>
</section>

<section class="banner banner--wide">
  <div class="singer-photo" role="img" aria-label="Photo of the band's singer performing at a microphone stand, tinted pink and cyan"></div>
  <div class="band-name">Slick Boot</div>
  <svg class="event-badge" viewBox="0 0 400 390" role="img" aria-label="Anniversary Gig, 20 Years of Funk! Saturday, August 10, 2024. With special guest Marco Delven. Doors at 7pm, show at 8pm"><use href="#event-badge"/></svg>
</section>

<section class="banner banner--square">
  <div class="singer-photo" role="img" aria-label="Photo of the band's singer performing at a microphone, tinted pink and cyan"></div>
  <div class="band-badge"><span class="band-badge__name">Slick Boot</span></div>
  <svg class="event-badge" viewBox="0 0 400 390" role="img" aria-label="Anniversary Gig, 20 Years of Funk! Saturday, August 10, 2024. With special guest Marco Delven. Doors at 7pm, show at 8pm"><use href="#event-badge"/></svg>
</section>

</body>
</html>
```